Maplecrest Disability - Social Security Disability Attorneys

Our company is expanding to attract clients nationwide for our social security disability practice. We have a logo, but I am looking for a creative and elegant letterhead that projects an image of being technologically advanced but still professional enough for the legal field. I am looking for the "wow factor" combined with this is still professional enough for a law practice.

Requesting letterhead and business card design
Updates

Had to update and change the logo. The previous logo had a typo. Please send updates with the new logo for consideration. The letterhead and business cards should be professional enough to be used for a law firm. Thanks.

Industry/Entity Type

Law Practice, Law Firm, Healthcare Industry, Government

Colors

Designer to choose colors to be used in the design.

Requirements
Nice to have
• **Please create a vertical design for the business card**

```html
<!DOCTYPE html>
<html lang="en">
<head>
<meta charset="utf-8">
<title>Maplecrest Disability – Letterhead</title>
<link href="https://fonts.googleapis.com/css2?family=Lato:wght@400;700&family=Satisfy&display=swap" rel="stylesheet">
<style>
  :root {
    --backdrop: #e9e9ea;
    --paper: #ffffff;
    --brand-blue: #5571bb;
    --accent-orange: #f08a30;
    --ink: #333333;
    --ink-soft: #4a4a4a;
  }
  * { margin: 0; padding: 0; box-sizing: border-box; }
  html, body {
    width: 1200px; height: 960px; overflow: hidden;
    background: var(--backdrop);
    font-family: "Lato", sans-serif;
    color: var(--ink);
  }
  .letterhead {
    position: absolute; left: 282px; top: 30px;
    width: 636px; height: 900px;
    background: var(--paper);
    box-shadow: 0 6px 24px rgba(0,0,0,.12);
    overflow: hidden;
  }
  .brand {
    position: absolute; left: 48px; top: 58px;
    display: flex; align-items: center; gap: 8px;
  }
  .brand-dot {
    width: 14px; height: 14px; border-radius: 50%;
    background: var(--accent-orange);
  }
  .brand-text { color: var(--brand-blue); font-weight: 400; line-height: 1.2; }
  .brand-name { font-size: 19px; letter-spacing: 2px; text-transform: uppercase; }
  .brand-tagline { font-size: 7px; letter-spacing: 1.6px; text-transform: uppercase; }

  .contact {
    position: absolute; right: 48px; top: 46px;
    padding-left: 12px;
    border-left: 1px solid var(--accent-orange);
    font-size: 9px; line-height: 1.55; color: var(--ink);
  }
  .contact-row { display: flex; align-items: center; gap: 6px; }
  .contact-row svg { width: 9px; height: 9px; fill: var(--accent-orange); flex: none; }

  .letter { position: absolute; left: 48px; top: 180px; width: 420px; font-size: 11px; line-height: 1.45; }
  .date { margin-bottom: 18px; font-size: 12px; }
  .recipient { margin-bottom: 14px; font-size: 12px; }
  .address { margin-bottom: 22px; font-size: 12px; }
  .salutation { font-size: 15px; font-weight: 700; margin-bottom: 14px; }
  .letter p.body { margin-bottom: 16px; color: var(--ink-soft); }
  .closing { margin-top: 22px; font-size: 11px; }
  .signature { font-family: "Satisfy", cursive; font-size: 38px; margin-top: 6px; color: #2a2a2a; }

  .pattern-area {
    position: absolute; right: 0; top: 400px;
    width: 200px; height: 460px;
    background: linear-gradient(to left, var(--brand-blue) 0%, rgba(85,113,187,.55) 45%, rgba(85,113,187,0) 100%);
  }
</style>
</head>
<body>
  <main class="letterhead">
    <header>
      <div class="brand">
        <span class="brand-dot"></span>
        <div class="brand-text">
          <div class="brand-name">Maplecrest Disability</div>
          <div class="brand-tagline">Social Security Disability Attorneys</div>
        </div>
      </div>
      <address class="contact" style="font-style:normal">
        <div>Suite 4, Level 12, Harbour Lane</div>
        <div>Brookvale NSW 2100</div>
        <div class="contact-row">
          <svg viewBox="0 0 10 10"><path d="M2 0.5l2 2-1 1.2c.6 1.2 1.5 2.1 2.7 2.7L6.9 5.4l2 2-1.3 1.6C4.6 9 1 5.4 1 1.8z"/></svg>
          555-014-2297
        </div>
        <div class="contact-row">
          <svg viewBox="0 0 10 10"><path d="M0.5 2h9v6h-9z M0.5 2l4.5 3.5L9.5 2" fill="none" stroke="#f08a30" stroke-width="1"/></svg>
          info@maplecrestdisability.com
        </div>
        <div class="contact-row">
          <svg viewBox="0 0 10 10"><circle cx="5" cy="5" r="4.5"/></svg>
          www.maplecrestdisability.com
        </div>
      </address>
    </header>

    <section class="letter">
      <div class="date">January-03-2020</div>
      <div class="recipient">Mr. Daniel Rowe<br>President</div>
      <div class="address">Fernway Corporation<br>123 Street Name, Suite# 10<br>City, State, 120023</div>
      <div class="salutation">Dear Mr. Rowe</div>
      <p class="body">Lorem ipsum dolor sit amet, consectetur adipisicing elit, sed do eiusmod tempor incididunt ut labore et dolore magna aliqua. Ut enim ad minim veniam, quis nostrud exercitation ullamco laboris nisi ut aliquip ex ea commodo consequat. Duis aute irure dolor in reprehenderit in voluptate velit esse cillum dolore eu fugiat nulla pariatur.</p>
      <p class="body">Lorem ipsum dolor sit amet, consectetur adipisicing elit, sed do eiusmod tempor incididunt ut labore et dolore magna aliqua. Ut enim ad minim veniam, quis nostrud exercitation ullamco laboris nisi ut aliquip ex ea commodo consequat. Duis aute irure dolor in reprehenderit in voluptate velit esse cillum dolore eu fugiat nulla pariatur.</p>
      <p class="body">Lorem ipsum dolor sit amet, consectetur adipisicing elit, sed do eiusmod tempor incididunt ut labore et dolore magna aliqua. Ut enim ad minim veniam, quis nostrud exercitation ullamco laboris nisi ut aliquip ex ea commodo consequat.</p>
      <p class="body">Excepteur sint occaecat cupidatat non proident, sunt in culpa qui officia deserunt mollit anim id est laborum. re et dolore magnam aliquam quaerat voluptatem.</p>
      <div class="closing">Regards</div>
      <div class="signature">Owen Hartley</div>
    </section>

    <div class="pattern-area" role="img" aria-label="Decorative pattern of blue triangles fading toward the left along the lower right edge"></div>
  </main>
</body>
</html>
```